American cannabis tech company business card design

Pavrel.com is seeking a modern, professional, and brand-aligned business card that represents our company and its core values: Mission, Story, Values, and Impact. As an innovative cannabis company, we want a business card that is not only visually appealing but also serves as a representation of who we are and what we stand for.

Project Scope: Design a double-sided business card that integrates our brand identity and core values. Incorporate our key brand elements, ensuring a sleek and contemporary aesthetic. Visually reflect our core values (Mission, Story, Values, Impact) in a way that is engaging yet professional.

Target Market(s)

Vendors, third parties,

Contact Information for Business Card

Contact details (name, title, email, phone, website, etc.)

Font styles to use
Other font styles liked:
• Caslon, Centra

Colors

Designer to choose colors to be used in the design.

Requirements
Must have
• Pavrel.com logo and branding A creative yet clean way to integrate our core values (Mission, Story, Values, Impact) Modern typography and a well-structured layout
Nice to have
• forest green, grey, white, black
Should not have
• references to marijuana, leafs, plants, or related product

```html
<!DOCTYPE html>
<html lang="en">
<head>
<meta charset="utf-8">
<title>Pavrel.com Business Card</title>
<link rel="stylesheet" href="https://fonts.googleapis.com/css2?family=Archivo:wght@400;600;800&display=swap">
<style>
  :root {
    --forest: #163a1d;
    --forest-deep: #112e17;
    --forest-light: #2c6a35;
    --white: #ffffff;
    --backdrop: #cfcfcf;
    --ink: #163a1d;
  }
  * { margin: 0; padding: 0; box-sizing: border-box; }
  html, body { width: 1200px; height: 800px; overflow: hidden; }
  body {
    background: var(--backdrop);
    font-family: "Archivo", Arial, sans-serif;
    position: relative;
  }
  .card {
    position: absolute;
    top: 245px;
    width: 540px;
    height: 310px;
    border-radius: 18px;
    overflow: hidden;
  }
  .card--front { left: 40px; background: var(--white); }
  .card--back  { left: 620px; background: var(--forest); }

  .holder { position: absolute; left: 34px; top: 78px; color: var(--ink); }
  .holder__name { font-size: 22px; font-weight: 800; letter-spacing: 0.5px; }
  .holder__title { font-size: 13px; font-weight: 400; letter-spacing: 0.6px; margin-top: 2px; }

  .contact-band {
    position: absolute; left: 0; top: 170px;
    width: 300px; height: 92px;
    background: var(--forest);
    padding: 14px 0 0 34px;
    color: var(--white);
  }
  .contact-band li {
    list-style: none; display: flex; align-items: center;
    font-size: 14px; line-height: 21px; letter-spacing: 0.3px;
  }
  .contact-band svg { width: 13px; height: 13px; margin-right: 7px; flex: none; }

  .brand-block {
    position: absolute; right: 34px; top: 34px;
    width: 96px; height: 78px;
    background: var(--forest);
  }
  .wordmark {
    position: absolute; font-weight: 800; letter-spacing: 1px;
  }
  .card--front .wordmark { left: 318px; top: 150px; font-size: 40px; color: var(--forest); }

  .pattern-field {
    position: absolute; inset: 0;
    background: linear-gradient(200deg, var(--forest-light) 0%, var(--forest) 45%, var(--forest-deep) 100%);
  }
  .card--back .wordmark { left: 352px; top: 172px; font-size: 28px; color: var(--white); }
</style>
</head>
<body>
  <section class="card card--front" aria-label="Business card front">
    <div class="holder">
      <p class="holder__name">DANIEL HART</p>
      <p class="holder__title">MANAGING DIRECTOR</p>
    </div>
    <ul class="contact-band">
      <li>
        <svg viewBox="0 0 16 16" aria-hidden="true"><path fill="#fff" d="M3.5 1.5l2.5 0 1 3.5-1.7 1.2a9 9 0 0 0 4.5 4.5L11 9l3.5 1v2.5c0 1-1 2-2 2A11.5 11.5 0 0 1 1.5 3.5c0-1 1-2 2-2z"/></svg>
        044-987 654 321
      </li>
      <li>
        <svg viewBox="0 0 16 16" aria-hidden="true"><rect x="1" y="3" width="14" height="10" fill="#fff"/><path d="M1 3l7 6 7-6" fill="none" stroke="#163a1d" stroke-width="1.3"/></svg>
        info@pavrel.com
      </li>
      <li>
        <svg viewBox="0 0 16 16" aria-hidden="true"><circle cx="8" cy="8" r="7" fill="#fff"/><g fill="none" stroke="#163a1d" stroke-width="1"><ellipse cx="8" cy="8" rx="3" ry="7"/><path d="M1 8h14M2.5 4.5h11M2.5 11.5h11"/></g></svg>
        www.pavrel.com
      </li>
    </ul>
    <p class="wordmark">PAVREL</p>
    <div class="brand-block"></div>
  </section>

  <section class="card card--back" aria-label="Business card back">
    <div class="pattern-field" role="img" aria-label="Repeating tone-on-tone brand name pattern in shades of forest green"></div>
    <p class="wordmark">PAVREL</p>
  </section>
</body>
</html>
```